Prime Global Casting Agency Needs creative business card design

We manage actors careers and book them liaising and promoting their profiles internationally through Casting Directors, Producers, Directors, Publicists etc. We need clearly visable contact details but with a design that reflects our status and creativity of TV, Feature Film industry. Our logo is attached and needs to relate and our website is www.brisklanestagefolk.com
No flame designs please but please incorporate logo colours.

Target Market(s)

Clients

Industry/Entity Type

Film Production

Contact Information for Business Card

Director Danielle Prowse
Suite F, Building 4, Wrenlow Studios Australia, Kelby Vale, Sydney, NSW 2048

Font styles to use
Sans Serif

Colors
ec1f27

Requirements
Nice to have
• Colours should relate to logo attached and type can relate again to type in the logo design.
Should not have
• No Flames designs and best to be not too obvious with the film designs eiither. Needs to be more creative and modern

```html
<!DOCTYPE html>
<html lang="en">
<head>
<meta charset="utf-8">
<title>Brisklane Stagefolk – Business Card</title>
<link rel="stylesheet" href="https://fonts.googleapis.com/css2?family=Exo+2:wght@400;500;600;800&display=swap">
<style>
  :root {
    --brand-red: #ec1f27;
    --deep-red: #b81c25;
    --card-white: #ffffff;
    --paper-grey: #eeeeee;
    --ink: #2b2b2b;
    --ink-soft: #555555;
    --rule: #222222;
    --backdrop: #d9d6d1;
    --photo-light: #e9c9a8;
    --photo-dark: #8a6a55;
    --social-grey: #9aa3ad;
  }
  html, body {
    margin: 0;
    width: 1200px;
    height: 885px;
    overflow: hidden;
    background: var(--backdrop);
    font-family: "Exo 2", sans-serif;
  }
  .stage { position: relative; width: 1200px; height: 885px; }

  .card {
    position: absolute;
    width: 560px;
    height: 320px;
    border-radius: 16px;
    box-shadow: 0 10px 24px rgba(0,0,0,0.25);
    overflow: hidden;
    box-sizing: border-box;
  }

  /* Front */
  .card-front {
    left: 50px; top: 90px;
    background: linear-gradient(135deg, var(--card-white) 0%, var(--paper-grey) 100%);
    color: var(--ink);
  }
  .front-logo { position: absolute; left: 32px; top: 42px; }
  .front-logo .wordmark {
    font-weight: 800; font-size: 44px; line-height: 1;
    letter-spacing: 1px; color: var(--brand-red);
  }
  .front-logo .tagline {
    font-weight: 800; font-size: 14px; color: var(--brand-red);
    margin-top: 4px; text-align: right;
  }
  .social { position: absolute; left: 32px; top: 126px; display: flex; gap: 10px; }
  .social span { width: 26px; height: 26px; border-radius: 4px; background: var(--social-grey); display: block; }
  .portrait {
    position: absolute; right: 40px; top: 26px;
    width: 132px; height: 92px;
    border: 2px solid #cfcfcf; border-radius: 4px;
    background: linear-gradient(135deg, var(--photo-light), var(--photo-dark));
  }
  .person { position: absolute; right: 40px; top: 128px; text-align: right; }
  .person .name { font-weight: 600; font-size: 24px; color: var(--brand-red); line-height: 1.1; }
  .person .role { font-weight: 500; font-size: 18px; color: var(--ink); }
  .divider { position: absolute; left: 32px; right: 40px; top: 186px; height: 1px; background: var(--rule); }
  .contacts { position: absolute; left: 32px; top: 206px; list-style: none; margin: 0; padding: 0; }
  .contacts li { display: flex; align-items: center; gap: 8px; font-size: 15px; height: 26px; color: var(--ink); }
  .contacts svg { width: 18px; height: 18px; flex: none; }
  .address {
    position: absolute; right: 40px; top: 206px; text-align: right;
    font-size: 15px; line-height: 26px; color: var(--ink);
  }

  /* Back */
  .card-back {
    left: 590px; top: 475px;
    background: linear-gradient(160deg, var(--brand-red) 0%, var(--deep-red) 100%);
    color: var(--card-white);
  }
  .back-logo { position: absolute; left: 50px; top: 112px; }
  .back-logo .wordmark { font-weight: 800; font-size: 70px; line-height: 1; letter-spacing: 2px; color: var(--card-white); }
  .back-logo .tagline { font-weight: 800; font-size: 20px; color: var(--card-white); text-align: right; margin-top: 4px; }
  .back-web { position: absolute; left: 50px; top: 40px; font-size: 16px; font-style: italic; letter-spacing: 0.5px; }
  .back-rule { position: absolute; height: 2px; background: var(--card-white); }
  .back-rule.top { left: 50px; top: 68px; width: 60px; }
  .back-rule.long { left: 320px; top: 70px; width: 190px; opacity: 0.8; }
</style>
</head>
<body>
<main class="stage">
  <section class="card card-front" aria-label="Business card front">
    <div class="front-logo">
      <div class="wordmark">BRISKLANE</div>
      <div class="tagline">Stagefolk</div>
    </div>
    <div class="social" aria-label="Social links">
      <span></span><span></span>
    </div>
    <div class="portrait" role="img" aria-label="Portrait photograph of Danielle Prowse"></div>
    <div class="person">
      <div class="name">Danielle Prowse</div>
      <div class="role">Director</div>
    </div>
    <div class="divider"></div>
    <ul class="contacts">
      <li>
        <svg viewBox="0 0 18 18"><rect width="18" height="18" rx="3" fill="#ec1f27"/><path d="M5 4h2.5l1 3-1.5 1c.7 1.4 1.6 2.3 3 3l1-1.5 3 1V13c0 .6-.4 1-1 1C8 14 4 10 4 5c0-.6.4-1 1-1z" fill="#fff"/></svg>
        +61 (0) 400 555 019
      </li>
      <li>
        <svg viewBox="0 0 18 18"><rect width="18" height="18" rx="3" fill="#ec1f27"/><rect x="3.5" y="5" width="11" height="8" fill="none" stroke="#fff" stroke-width="1.3"/><path d="M3.5 5l5.5 4.5L14.5 5" fill="none" stroke="#fff" stroke-width="1.3"/></svg>
        danielle@brisklanestagefolk.com
      </li>
      <li>
        <svg viewBox="0 0 18 18"><rect width="18" height="18" rx="3" fill="#ec1f27"/><circle cx="9" cy="9" r="5" fill="none" stroke="#fff" stroke-width="1.2"/><ellipse cx="9" cy="9" rx="2.2" ry="5" fill="none" stroke="#fff" stroke-width="1"/><path d="M4 9h10" stroke="#fff" stroke-width="1"/></svg>
        www.brisklanestagefolk.com
      </li>
    </ul>
    <address class="address" style="font-style:normal">
      Suite F, Building 4,<br>
      Wrenlow Studios Australia,<br>
      Kelby Vale, Sydney, NSW 2048
    </address>
  </section>

  <section class="card card-back" aria-label="Business card back">
    <div class="back-web">www.brisklanestagefolk.com</div>
    <div class="back-rule top"></div>
    <div class="back-rule long"></div>
    <div class="back-logo">
      <div class="wordmark">BRISKLANE</div>
      <div class="tagline">Stagefolk</div>
    </div>
  </section>
</main>
</body>
</html>
```